Stonebridge Building and Projects business cards

A business card with watermark background (construction work)

Company logo attached

Home improvement projects
House renovations
Bathroom and kitchen renovations
House extensions
New builds and granny flats

Director Omar Haddani
(Phone number)
omar@sbpbuilding.com.au
(Instagram logo) sbp_building

```html
<!DOCTYPE html>
<html lang="en">
<head>
<meta charset="utf-8">
<title>Stonebridge Building and Projects – Business Cards</title>
<link href="https://fonts.googleapis.com/css2?family=Montserrat:wght@500;600&family=Arimo:wght@400&display=swap" rel="stylesheet">
<style>
  :root {
    --backdrop: #2b2b2d;
    --card: #1c1d20;
    --brand-blue: #3a7bc8;
    --ink-light: #f2f2f2;
    --rule: #8a8a8a;
    --pattern-dark: #222326;
    --pattern-light: #303135;
  }
  * { margin: 0; padding: 0; box-sizing: border-box; }
  html, body { width: 1200px; height: 1108px; overflow: hidden; }
  body {
    background: var(--backdrop);
    position: relative;
    font-family: "Arimo", Arial, sans-serif;
    color: var(--ink-light);
  }
  .card {
    position: absolute;
    top: 214px;
    width: 440px;
    height: 680px;
    background: var(--card);
    border-radius: 26px;
    overflow: hidden;
    box-shadow: 0 18px 40px rgba(0,0,0,.45);
  }
  .card--front { left: 120px; }
  .card--back { left: 640px; }

  /* Front */
  .brand-name {
    position: absolute;
    top: 92px; left: 0; right: 0;
    text-align: center;
    font-family: "Montserrat", sans-serif;
    font-weight: 600;
    color: var(--brand-blue);
    font-size: 42px;
    line-height: 1.12;
  }
  .brand-rule {
    position: absolute;
    top: 262px; left: 70px; right: 70px;
    height: 2px; background: var(--brand-blue);
  }
  .holder {
    position: absolute; top: 318px; left: 0; right: 0; text-align: center;
  }
  .holder__name {
    font-family: "Montserrat", sans-serif; font-weight: 600;
    color: var(--brand-blue); font-size: 32px;
  }
  .holder__role { font-size: 22px; margin-top: 4px; }
  .divider {
    position: absolute; left: 60px; right: 60px;
    display: flex; align-items: center; gap: 10px;
  }
  .divider::before, .divider::after {
    content: ""; flex: 1; height: 1px; background: var(--rule);
  }
  .divider--contact { top: 430px; }
  .divider--social { top: 590px; }
  .icon-tile {
    width: 34px; height: 34px; border-radius: 5px;
    background: var(--brand-blue);
    display: flex; align-items: center; justify-content: center;
  }
  .contact-list {
    position: absolute; top: 482px; left: 0; right: 0;
    text-align: center; list-style: none;
    font-size: 22px; line-height: 1.42;
  }
  .contact-list .accent { color: var(--brand-blue); }
  .social-handle {
    position: absolute; top: 634px; left: 0; right: 0;
    text-align: center; font-size: 22px;
  }

  /* Back */
  .watermark-field {
    position: absolute; inset: 0;
    background: linear-gradient(160deg, var(--pattern-light) 0%, var(--pattern-dark) 55%, #1a1b1e 100%);
  }
  .back-content {
    position: absolute; top: 398px; left: 0; right: 0; text-align: center;
  }
  .back-content__brand {
    font-family: "Montserrat", sans-serif; font-weight: 600;
    color: var(--brand-blue); font-size: 24px; margin-bottom: 16px;
  }
  .services { list-style: none; font-size: 21px; line-height: 1.45; }
</style>
</head>
<body>

<section class="card card--front" aria-label="Card front">
  <h1 class="brand-name">Stonebridge<br>Building and<br>Projects</h1>
  <div class="brand-rule"></div>

  <div class="holder">
    <p class="holder__name">Omar Haddani</p>
    <p class="holder__role">Director</p>
  </div>

  <div class="divider divider--contact">
    <span class="icon-tile" aria-label="Phone">
      <svg width="20" height="20" viewBox="0 0 24 24"><path fill="#1c1d20" d="M6.6 10.8a15 15 0 0 0 6.6 6.6l2.2-2.2c.3-.3.7-.4 1-.2 1.1.4 2.3.6 3.6.6.6 0 1 .4 1 1V20c0 .6-.4 1-1 1A17 17 0 0 1 3 4c0-.6.4-1 1-1h3.5c.6 0 1 .4 1 1 0 1.3.2 2.5.6 3.6.1.3 0 .7-.2 1z"/></svg>
    </span>
    <span class="icon-tile" aria-label="Email">
      <svg width="20" height="16" viewBox="0 0 20 16"><rect x="1" y="1" width="18" height="14" fill="none" stroke="#1c1d20" stroke-width="2"/><path d="M1 1l9 8 9-8" fill="none" stroke="#1c1d20" stroke-width="2"/></svg>
    </span>
    <span class="icon-tile" aria-label="Website">
      <svg width="20" height="20" viewBox="0 0 20 20"><circle cx="10" cy="10" r="8" fill="none" stroke="#1c1d20" stroke-width="2"/><path d="M2 10h16M10 2c3 3 3 13 0 16M10 2c-3 3-3 13 0 16" fill="none" stroke="#1c1d20" stroke-width="1.5"/></svg>
    </span>
  </div>

  <ul class="contact-list">
    <li>044-555 210 347</li>
    <li>omar@sbpbuilding.com.au</li>
    <li>www.<span class="accent">sbpbuilding</span>.com.au</li>
  </ul>

  <div class="divider divider--social">
    <span class="icon-tile" aria-label="Social profile"></span>
  </div>
  <p class="social-handle">sbp_building</p>
</section>

<section class="card card--back" aria-label="Card back">
  <div class="watermark-field" role="img" aria-label="Faint repeating brand watermark pattern"></div>
  <div class="back-content">
    <p class="back-content__brand">Stonebridge</p>
    <ul class="services">
      <li>Home improvement projects</li>
      <li>House renovations</li>
      <li>Bathroom and kitchen renovations</li>
      <li>House extensions</li>
      <li>New builds and granny flats</li>
    </ul>
  </div>
</section>

</body>
</html>
```